zAvora Corporate Website

zAvora is a well-funded start up developing an Online Marketing Platform for small businesses in Europe.
We are launching in February 2012 with all-in-one online marketing services including professional website, DIY SEO, Dashboard with Reports and Online marketing tools, and Support.
Our internal web designer has come up with a preliminary website design which we wish to continue to improve using new ideas, colours, layout, image, etc.
The brief is very simple - improve the website whether it is look & feel, ease of use, conversion rate - we are looking for overall improvements.
The contest will last 5 days and we will award the winner £300.
If you are the winner , you will also be required to provide designs for 3 more internal pages adhering to the proposed home page design.
Judging criteria : -
Visual Design
Layout must adhere to best practices and wire frame. If you decide to move elements around significantly please provide reason
Functional, informative and drives calls to action
Industry/Entity Type
Marketing
Look and feel
Each slider illustrates characteristics of the customer's brand and the style your logo design should communicate.

```html
<!DOCTYPE html>
<html lang="en">
<head>
<meta charset="utf-8">
<title>zAvora – Online Marketing for Small Business</title>
<link href="https://fonts.googleapis.com/css2?family=Open+Sans:ital,wght@0,400;0,600;0,700;0,800;1,400;1,700;1,800&display=swap" rel="stylesheet">
<style>
:root{
  --navy:#061a4e;
  --navy-2:#0d2a6e;
  --login:#1a3372;
  --orange:#f08a12;
  --bubble:#fbb347;
  --orange-text:#e8650d;
  --green:#6aae3a;
  --text:#3c3c3c;
  --band:#b6d4ea;
  --shirt:#a9c7e6;
  --footer-bg:#e6f1f9;
  --footer-panel:#d6e7f4;
  --link:#1d3f7a;
  --news-blue:#1f91d8;
  --red:#b8141b;
  --blue:#0f2f72;
  --black:#111;
}
*{margin:0;padding:0;box-sizing:border-box}
html,body{width:977px;height:1200px;overflow:hidden;background:#fff}
body{font-family:"Open Sans",Arial,sans-serif;color:var(--text);position:relative}

/* header */
.site-header{position:absolute;left:0;top:0;width:977px;height:48px;background:linear-gradient(var(--navy-2),var(--navy))}
.brand{position:absolute;left:147px;top:8px;display:flex;align-items:center;gap:6px;color:#fff;font-size:26px;font-weight:600;line-height:32px}
.brand-dot{width:26px;height:26px;border-radius:50%;background:var(--orange)}
.main-nav a{position:absolute;top:15px;height:20px;line-height:20px;font-size:9.5px;color:#fff;text-decoration:none;letter-spacing:.2px}
.main-nav .active{background:#22407f;color:var(--orange);padding:0 9px;border-radius:2px}
.login{position:absolute;left:726px;top:0;width:104px;height:48px;background:var(--login)}
.login span{position:absolute;left:24px;top:15px;font-size:9.5px;color:#fff;line-height:18px}
.login i{position:absolute;left:60px;top:13px;width:22px;height:22px;border-radius:50%;background:var(--orange)}

/* hero */
.benefits{position:absolute;left:147px;top:77px;list-style:none}
.benefits li{height:25px;line-height:17px;font-size:12.5px;color:var(--green);padding-left:17px;position:relative}
.benefits li svg{position:absolute;left:0;top:3px}
.hero-title{position:absolute;left:147px;top:195px;width:190px;font-size:13px;font-weight:400;line-height:16px;color:#333}
.cta{position:absolute;left:147px;top:238px;width:102px;height:38px;border-radius:4px;background:linear-gradient(#a9a9a9,#6e6e6e);border:1px solid #5c5c5c;color:#fff;text-align:center}
.cta small{display:block;font-size:8px;margin-top:5px;line-height:10px}
.cta b{display:block;font-size:14px;font-weight:800;line-height:16px}
.hero-visual{position:absolute;left:370px;top:52px;width:460px;height:264px;
  background:
    radial-gradient(ellipse 95px 120px at 340px 190px,var(--shirt) 0%,rgba(169,199,230,.6) 55%,rgba(169,199,230,0) 100%),
    radial-gradient(ellipse 120px 40px at 110px 60px,rgba(251,179,71,.55) 0%,rgba(251,179,71,0) 100%),
    radial-gradient(ellipse 90px 40px at 370px 40px,rgba(251,179,71,.5) 0%,rgba(251,179,71,0) 100%),
    radial-gradient(ellipse 60px 80px at 400px 160px,rgba(251,179,71,.4) 0%,rgba(251,179,71,0) 100%),
    radial-gradient(ellipse 60px 50px at 60px 160px,rgba(251,179,71,.4) 0%,rgba(251,179,71,0) 100%),
    radial-gradient(ellipse at 60% 70%,#eef4fa 0%,#fff 75%)}
.slide-arrow{position:absolute;top:279px;width:20px;height:20px;background:#cfd3d7;border:1px solid #b8bcc0}
.slide-arrow svg{display:block;margin:4px auto}
.band{position:absolute;left:147px;top:316px;width:683px;height:48px;background:var(--band);text-align:center}
.band-tab{position:absolute;left:147px;top:304px;width:0;height:0;border-left:9px solid var(--band);border-top:12px solid transparent}
.band h1{font-size:16px;font-style:italic;font-weight:700;color:#fff;line-height:20px;margin-top:7px}
.band p{font-size:12px;color:#2c3e55;line-height:16px}

/* features */
.features{position:absolute;left:0;top:378px;width:977px;height:107px;background:linear-gradient(#fafafa,#e4e4e4);border-top:1px solid #d3d3d3;border-bottom:1px solid #d3d3d3}
.feature{position:absolute;top:0;height:105px;text-align:center}
.feature h2{position:absolute;left:0;right:0;top:48px;font-size:12.5px;font-weight:700;color:#111}
.feature p{position:absolute;left:0;right:0;top:73px;font-size:8.5px;line-height:11px;color:#555}
.feature .icon{position:absolute;top:9px;left:50%;transform:translateX(-50%)}
.divider{position:absolute;top:0;width:1px;height:105px;background:linear-gradient(#fff,#cfcfcf,#fff)}

/* offers */
.offer{position:absolute;top:505px;width:159px;height:125px;background:linear-gradient(#ffffff,#ececec);border:1px solid #dcdcdc;box-shadow:0 2px 2px rgba(0,0,0,.15)}
.ribbon{position:absolute;left:15px;top:-1px;width:30px;height:131px}
.seal{position:absolute;left:5px;top:27px;width:52px;height:52px;border-radius:50%;color:#fff;text-align:center;font-size:15px;line-height:17px;padding-top:10px;border:3px dotted rgba(255,255,255,.25)}
.seal small{display:block;font-size:6px;color:#f7d21a;font-weight:700;line-height:7px}
.offer h3{position:absolute;left:60px;top:13px;font-size:13.5px;font-weight:800;line-height:16px;color:#111}
.offer .note{position:absolute;left:62px;font-size:9px;line-height:11px;color:#222}
.offer .tag{position:absolute;right:0;top:97px;height:16px;line-height:16px;padding:0 7px;font-size:7.5px;font-weight:700;color:#fff}
.how{position:absolute;left:668px;top:505px;width:162px;height:125px;border:1px solid #d5d5d5;background:#fff}
.how h4{height:26px;line-height:26px;padding-left:8px;background:linear-gradient(#fff,#e5e5e5);border-bottom:1px solid #d5d5d5;font-size:10.5px;font-weight:700;color:var(--link)}
.how p{padding:8px 9px 0;font-size:9px;line-height:12.5px;color:#333}
.how a{position:absolute;right:8px;bottom:8px;font-size:9px;color:var(--orange-text);text-decoration:none}

/* examples */
.examples-bar{position:absolute;left:147px;top:658px;width:683px;height:28px;background:#efefef}
.examples-bar h2{position:absolute;left:7px;top:6px;font-size:12.5px;font-weight:800;color:var(--orange-text)}
.small-arrow{position:absolute;top:8px;width:11px;height:11px;background:#b4b4b4}
.monitor{position:absolute;top:706px;width:143px;height:120px}
.quote{position:absolute;top:705px;width:158px;font-size:9px;line-height:14px;color:#555}
.quote p+p{margin-top:14px}
.quote-cite{position:absolute;top:818px;font-size:8px;color:var(--orange-text);font-style:italic;text-align:right;width:158px}
.visit{position:absolute;top:831px;font-size:8px;line-height:12px;color:#666;font-style:italic}

/* footer */
.site-footer{position:absolute;left:0;top:880px;width:977px;height:320px;background:var(--footer-bg)}
.footer-panel{position:absolute;left:153px;top:15px;width:670px;height:120px;background:var(--footer-panel)}
.footer-col{position:absolute;top:20px}
.footer-col h5{font-size:8.5px;font-weight:800;color:#111;margin-bottom:8px}
.footer-col ul{list-style:none;border-left:1px solid #93b4cf;margin-left:-14px;padding-left:13px}
.footer-col li{font-size:8px;line-height:12px;color:var(--link);position:relative}
.footer-col li::before{content:"";position:absolute;left:-6px;top:5px;width:2px;height:2px;background:#6d8fae}
.newsletter{position:absolute;left:472px;top:21px;width:180px;height:74px;border:2px solid var(--news-blue);background:var(--footer-panel)}
.newsletter h5{position:absolute;left:-2px;top:-4px;background:var(--footer-panel);padding-right:5px;font-size:10.5px;font-weight:400;color:#111}
.newsletter .field{position:absolute;left:9px;top:22px;width:104px;height:18px;background:#fff;border:1px solid #c9c9c9;font-size:8px;font-style:italic;color:#999;line-height:16px;padding-left:6px}
.newsletter .submit{position:absolute;left:119px;top:22px;width:46px;height:18px;background:var(--orange);color:#fff;font-size:8px;font-weight:700;line-height:18px;text-align:center}
.newsletter .share{position:absolute;left:11px;top:49px;height:13px;padding:0 4px 0 3px;border:1px solid #bbb;border-radius:2px;background:#fff;font-size:7.5px;line-height:11px;color:#333}
.newsletter .friend{position:absolute;left:68px;top:48px;font-size:8px;line-height:14px;color:#333}
.newsletter .friend i{display:inline-block;width:12px;height:12px;background:#3a5a98;vertical-align:-3px;margin-right:6px}
.about{position:absolute;left:147px;top:147px;width:683px;text-align:center;font-size:7.6px;line-height:12.5px;color:#555}
.about p+p{margin-top:12px}
.copyright{position:absolute;left:147px;top:285px;width:683px;border-top:1px solid #c5d6e3;padding-top:11px;font-size:8px;color:#555}
.social{position:absolute;top:292px;width:12px;height:12px}
</style>
</head>
<body>

<header class="site-header">
  <div class="brand"><span class="brand-dot"></span>zAvora</div>
  <nav class="main-nav">
    <a class="active" style="left:371px">HOME</a>
    <a style="left:430px">QUICK TOUR</a>
    <a style="left:510px">PRICING</a>
    <a style="left:571px">ABOUT US</a>
    <a style="left:642px">CONTACT US</a>
  </nav>
  <div class="login"><span>LOGIN</span><i></i></div>
</header>

<ul class="benefits">
  <li><svg width="11" height="11" viewBox="0 0 11 11"><circle cx="5.5" cy="5.5" r="4.8" fill="none" stroke="#aaa"/><path d="M3 5.6l1.8 1.8L8 3.8" fill="none" stroke="#999" stroke-width="1.2"/></svg>BUSINESS WEBSITE</li>
  <li><svg width="11" height="11" viewBox="0 0 11 11"><circle cx="5.5" cy="5.5" r="4.8" fill="none" stroke="#aaa"/><path d="M3 5.6l1.8 1.8L8 3.8" fill="none" stroke="#999" stroke-width="1.2"/></svg>ONLINE MARKETING</li>
  <li><svg width="11" height="11" viewBox="0 0 11 11"><circle cx="5.5" cy="5.5" r="4.8" fill="none" stroke="#aaa"/><path d="M3 5.6l1.8 1.8L8 3.8" fill="none" stroke="#999" stroke-width="1.2"/></svg>DASHBOARD CONTROLS</li>
  <li><svg width="11" height="11" viewBox="0 0 11 11"><circle cx="5.5" cy="5.5" r="4.8" fill="none" stroke="#aaa"/><path d="M3 5.6l1.8 1.8L8 3.8" fill="none" stroke="#999" stroke-width="1.2"/></svg>FULL SETUP &amp; SUPPORT</li>
</ul>
<h2 class="hero-title">GETTING A WEBSITE HAS NEVER BEEN SO SIMPLE</h2>
<div class="cta"><small>SIGN UP NOW FOR</small><b>FREE!</b></div>

<div class="hero-visual" role="img" aria-label="Puzzled businessman in a blue shirt surrounded by orange speech bubbles asking about SEO, blogs, banners, social media and other online marketing questions"></div>
<div class="slide-arrow" style="left:785px"><svg width="10" height="10" viewBox="0 0 10 10"><path d="M9 5H1M4 2L1 5l3 3" fill="none" stroke="#fff" stroke-width="1.2"/></svg></div>
<div class="slide-arrow" style="left:809px"><svg width="10" height="10" viewBox="0 0 10 10"><path d="M1 5h8M6 2l3 3-3 3" fill="none" stroke="#fff" stroke-width="1.2"/></svg></div>

<div class="band-tab"></div>
<section class="band">
  <h1>THE COMPLETE ONLINE MARKETING SOLUTION FOR SMALL BUSINESS WEBSITES</h1>
  <p>“Get a big online presence and more sales leads in 30 minutes”</p>
</section>

<section class="features">
  <div class="feature" style="left:148px;width:160px">
    <svg class="icon" width="40" height="38" viewBox="0 0 40 38"><rect x="2" y="2" width="10" height="34" fill="#5aa524"/><rect x="14" y="20" width="10" height="16" fill="#d92a1a"/><rect x="26" y="10" width="10" height="26" fill="#f2a20f"/></svg>
    <h2>CASE STUDIES</h2><p>Read real stories about small<br>business online...</p>
  </div>
  <div class="divider" style="left:311px"></div>
  <div class="feature" style="left:319px;width:160px">
    <svg class="icon" width="28" height="38" viewBox="0 0 28 38" role="img" aria-label="Light bulb icon"><circle cx="14" cy="13" r="12" fill="#f7d11e"/><rect x="9" y="26" width="10" height="8" fill="#aaa"/></svg>
    <h2>HOW TO</h2><p>Learn from our online marketin<br>tips for small business...</p>
  </div>
  <div class="divider" style="left:489px"></div>
  <div class="feature" style="left:493px;width:160px">
    <svg class="icon" width="34" height="34" viewBox="0 0 34 34" role="img" aria-label="Chat bubbles icon"><ellipse cx="20" cy="12" rx="12" ry="9" fill="#2b9ad8"/><ellipse cx="13" cy="21" rx="11" ry="8" fill="#3fae3a"/></svg>
    <h2>NEWS &amp; CHATTER</h2><p>Get up to-date news &amp; chatter<br>about online marketing...</p>
  </div>
  <div class="divider" style="left:661px"></div>
  <div class="feature" style="left:669px;width:160px">
    <svg class="icon" width="34" height="34" viewBox="0 0 34 34" role="img" aria-label="Presenter with clock icon"><rect x="2" y="4" width="22" height="28" rx="4" fill="#4b4f57"/><circle cx="24" cy="22" r="8" fill="#b9c8d6"/></svg>
    <h2>DEMO</h2><p>Find out what zAvora can do<br>for your business...</p>
  </div>
</section>

<article class="offer" style="left:147px">
  <div class="ribbon" style="background:var(--red)"></div>
  <div class="seal" style="background:var(--red)">£ 199<small>VALUE</small></div>
  <h3>FREE SET UP</h3>
  <div class="note" style="top:67px">WEB OFFER ONLY</div>
  <div class="tag" style="background:var(--red)">FREE</div>
</article>
<article class="offer" style="left:321px">
  <div class="ribbon" style="background:var(--blue)"></div>
  <div class="seal" style="background:var(--blue)">£ 22<small>VALUE</small></div>
  <h3>BIG ONLINE<br>PRESENCE</h3>
  <div class="note" style="top:56px">BUSINESS WEBSITE<br>&amp; EASY DASHBOARD</div>
  <div class="tag" style="background:var(--blue)">PRO PACKAGE</div>
</article>
<article class="offer" style="left:495px">
  <div class="ribbon" style="background:var(--black)"></div>
  <div class="seal" style="background:var(--black)">£ 29<small>VALUE</small></div>
  <h3>MORE SALES<br>LEADS</h3>
  <div class="note" style="top:67px">WEB OFFER ONLY</div>
  <div class="tag" style="background:var(--black)">TURBO SALES PRO PLUS</div>
</article>
<aside class="how">
  <h4>HOW DOES IT WORKS?</h4>
  <p>Lorem Ipsum is simply dummy text of the printing and industry. Lorem Ipsum has been the industry's standard dummy text ever since the 1500s</p>
  <a>Read More ▸</a>
</aside>

<div class="examples-bar">
  <h2>VIEW EXAMPLES OF OUR STUNNING BUSINESS WEBSITES</h2>
  <div class="small-arrow" style="left:651px"></div>
  <div class="small-arrow" style="left:664px"></div>
</div>

<svg class="monitor" style="left:147px" viewBox="0 0 143 120" role="img" aria-label="Desktop monitor showing a sample business website">
  <rect x="0" y="0" width="143" height="88" rx="3" fill="#2b2b2b"/>
  <rect x="4" y="4" width="135" height="80" fill="#e9f1f8"/>
  <rect x="0" y="88" width="143" height="12" fill="#d8d8d8"/>
  <path d="M55 100h33l4 14H51z" fill="#c4c4c4"/>
  <ellipse cx="71" cy="116" rx="34" ry="3" fill="#ddd"/>
</svg>
<div class="quote" style="left:315px">
  <p>Lorem Ipsum is simply dummy text of the typesetting industry.</p>
  <p>Lorem Ipsum has been. The industry's standard dummy text ever since the 1500s, when an unknown printer took a galley of type.</p>
</div>
<div class="quote-cite" style="left:312px">-Lorem Ipsum Text</div>
<div class="visit" style="left:147px">Visit Website:<br>http://www.zavora.com/</div>

<svg class="monitor" style="left:506px" viewBox="0 0 143 120" role="img" aria-label="Desktop monitor showing a sample business website">
  <rect x="0" y="0" width="143" height="88" rx="3" fill="#2b2b2b"/>
  <rect x="4" y="4" width="135" height="80" fill="#e9f1f8"/>
  <rect x="0" y="88" width="143" height="12" fill="#d8d8d8"/>
  <path d="M55 100h33l4 14H51z" fill="#c4c4c4"/>
  <ellipse cx="71" cy="116" rx="34" ry="3" fill="#ddd"/>
</svg>
<div class="quote" style="left:675px">
  <p>Lorem Ipsum is simply dummy text of the typesetting industry.</p>
  <p>Lorem Ipsum has been. The industry's standard dummy text ever since the 1500s, when an unknown printer took a galley of type.</p>
</div>
<div class="quote-cite" style="left:671px">-Lorem Ipsum Text</div>
<div class="visit" style="left:506px">Visit Website:<br>http://www.zavora.com/</div>

<footer class="site-footer">
  <div class="footer-panel">
    <div class="footer-col" style="left:33px">
      <h5>COMPANY</h5>
      <ul><li>Search Marketing -<br>Organic / Natural (SEO)</li><li>Social Media</li><li>Web Anaytics</li></ul>
    </div>
    <div class="footer-col" style="left:188px">
      <h5>CUSTOMER SERVICES</h5>
      <ul><li>Contact Us</li><li>Customer Support</li><li>Request a Call Back</li><li>FAQ's</li></ul>
    </div>
    <div class="footer-col" style="left:357px">
      <h5>INFORMATION</h5>
      <ul style="height:58px"><li>Site Map</li><li>Terms &amp; Conditions</li></ul>
    </div>
    <div class="newsletter">
      <h5>Subscribe for Newsletter</h5>
      <div class="field">Your Email</div>
      <div class="submit">SUBMIT</div>
      <div class="share">Share</div>
      <div class="friend"><i></i>Become a Friend</div>
    </div>
  </div>

  <div class="about">
    <p>zAvora will build your business website, optimise SEP marketing and make recommendations on best practies to help you win customers. Let our team of experts design a business website for you. Choose a business website from zAvora's broad array of fabulous, customisable business websites and our experts will have your business onlune minutes. zAvora lets you create a professional business website without the need to know how to code or programme.</p>
    <p>Your business website comes with automatic Internet marketing, marketing on the Interned is easy with zAvora, we automatically optimise your site for SEO marketing and we can Searchly ad campaigns when you need them. Get a business website with online marketing not. zAvora brings your Small Business Website to LIFE!</p>
    <p>View our example business websites above, watch the video demo to see how to make a business website or call us now and get your business marketing online today. The zAvora website builder gives you a professional online appearance - post your own images, give customers your latest news and create customer testimonials, it's the most complete online marketing solution for your business.</p>
  </div>
  <div class="copyright">© 2012 zAvora Pvt. Ltd. All Rights Reserved.</div>
  <div class="social" style="left:803px;background:#3a5a98"></div>
  <div class="social" style="left:818px;background:#4fb3e6"></div>
</footer>

</body>
</html>
```